Single-sided business card for restaurant velmora with new logo made on this site

Business card options with new logo including restaurant name, address, phone number and website. This business card is single-sided only and will be presented at the hostess desk for clients to take. I would like to see options based on a cream card background, a white card background, a yellow card background and a burgundy colored background. It needs to be elegant and traditional.

Target Market(s)

local and international crowd

Industry/Entity Type

restaurant

Contact Information for Business Card

address, website and phone number

Font styles to use
Serif

Colors
EE7325
F08F49
F5BC92
FAE3D3
FDF4ED

Requirements
Must have
• new logo, address, phone number, website
Should not have
• more than three colors

```html
<!DOCTYPE html>
<html lang="es">
<head>
<meta charset="utf-8">
<title>Velmora – Tarjeta de presentación</title>
<link rel="stylesheet" href="https://fonts.googleapis.com/css2?family=Cinzel:wght@500&family=Crimson+Pro:wght@500&family=Arimo:wght@400&display=swap">
<style>
  :root {
    --backdrop: #2a2a2a;
    --card: #ffffff;
    --gold: #f2ab24;
    --maroon: #3b1a1c;
    --rule: #c9c9c9;
  }
  * { margin: 0; padding: 0; box-sizing: border-box; }
  html, body {
    width: 1200px; height: 900px; overflow: hidden;
    background: var(--backdrop);
  }
  .canvas {
    width: 1200px; height: 900px;
    display: flex; align-items: center; justify-content: center;
  }
  .business-card {
    position: relative;
    width: 1000px; height: 560px;
    background: var(--card);
    border: 7px solid var(--gold);
    box-shadow: 0 12px 30px rgba(0,0,0,.45);
  }
  .brand-block {
    position: absolute;
    left: 90px; top: 100px;
    width: 300px; height: 360px;
    display: flex; align-items: center; justify-content: center; gap: 14px;
  }
  .brand-mark {
    width: 22px; height: 22px;
    background: var(--gold);
  }
  .brand-name {
    font-family: "Cinzel", serif;
    font-weight: 500;
    font-size: 44px;
    letter-spacing: 6px;
    color: var(--maroon);
  }
  .divider {
    position: absolute;
    left: 450px; top: 150px;
    width: 1px; height: 270px;
    background: var(--rule);
  }
  .contact {
    position: absolute;
    left: 505px; top: 170px;
    color: var(--maroon);
  }
  .contact-label {
    font-family: "Cinzel", serif;
    font-weight: 500;
    font-size: 28px;
    letter-spacing: 1.5px;
    color: var(--gold);
    line-height: 1;
  }
  .contact-phone {
    font-family: "Crimson Pro", serif;
    font-weight: 500;
    font-size: 50px;
    letter-spacing: 1px;
    line-height: 1.05;
    margin-top: 4px;
  }
  .contact-web {
    font-family: "Arimo", sans-serif;
    font-size: 24px;
    margin-top: 22px;
  }
  .contact-address {
    font-family: "Arimo", sans-serif;
    font-size: 25px;
    line-height: 1.2;
    margin-top: 26px;
    font-style: normal;
  }
</style>
</head>
<body>
<main class="canvas">
  <section class="business-card">
    <div class="brand-block">
      <span class="brand-mark" aria-hidden="true"></span>
      <span class="brand-name">VELMORA</span>
    </div>
    <div class="divider" aria-hidden="true"></div>
    <div class="contact">
      <p class="contact-label">Reservaciones</p>
      <p class="contact-phone">958-214-3072</p>
      <p class="contact-web">www.velmora.com.mx</p>
      <address class="contact-address">
        Restaurant Velmora<br>
        Magnolia 517<br>
        Bahías de Huatulco<br>
        Oaxaca CP 70945
      </address>
    </div>
  </section>
</main>
</body>
</html>
```